Birchline Septic Solutions

Would like to see some single sided ones but would also like to see some double sided with one sided only being the logo. Owners name is Colin Vandro. Phone number is 555-214-0387
Services are pumping, inspections, installs, and repairs

Contact Information for Business Card

555-241-0387 Colin Vandro Maplecrest, OH

```html
<!DOCTYPE html>
<html lang="en">
<head>
<meta charset="utf-8">
<title>Birchline Septic Solutions – Business Card</title>
<link href="https://fonts.googleapis.com/css2?family=Montserrat:wght@500;600;700;800&display=swap" rel="stylesheet">
<style>
  :root {
    --backdrop: #e7e3dd;
    --card-light: #eef1f2;
    --card-light-edge: #dfe3e5;
    --card-dark: #1e1c1c;
    --ink: #1f1f1f;
    --teal: #1fa893;
    --teal-bright: #23c0b4;
    --tan: #b59a86;
    --cream: #e6dccf;
  }
  * { margin: 0; padding: 0; box-sizing: border-box; }
  html, body {
    width: 1200px; height: 897px; overflow: hidden;
    background: var(--backdrop);
    font-family: "Montserrat", Arial, sans-serif;
  }
  .canvas { position: relative; width: 1200px; height: 897px; }
  .card {
    position: absolute; left: 60px; top: 153px;
    width: 1080px; height: 590px;
    border-radius: 24px; overflow: hidden;
    box-shadow: 0 14px 40px rgba(0,0,0,0.12);
  }
  .card-art { position: absolute; inset: 0; }
  .brand-name {
    position: absolute; left: 0; right: 0; top: 150px;
    text-align: center;
    font-weight: 800; font-size: 44px; letter-spacing: 1px;
    color: var(--ink); text-transform: uppercase;
  }
  .owner {
    position: absolute; right: 580px; top: 436px; text-align: right;
    white-space: nowrap;
  }
  .owner-name {
    font-weight: 700; font-size: 50px; line-height: 1; letter-spacing: 0.5px;
    color: var(--teal); text-transform: uppercase;
  }
  .owner-town {
    margin-top: 12px;
    font-weight: 600; font-size: 28px; line-height: 1; letter-spacing: 0.5px;
    color: var(--tan);
  }
  .divider {
    position: absolute; left: 542px; top: 434px;
    width: 2px; height: 96px; background: var(--teal);
  }
  .phone {
    position: absolute; left: 582px; top: 461px;
    display: flex; align-items: center; gap: 14px;
    font-weight: 600; font-size: 40px; line-height: 1; letter-spacing: 0.5px;
    color: var(--cream); white-space: nowrap;
  }
  .phone-icon { width: 32px; height: 28px; }
</style>
</head>
<body>
<div class="canvas">
  <div class="card">
    <svg class="card-art" width="1080" height="590" viewBox="0 0 1080 590">
      <defs>
        <linearGradient id="frost" x1="0" y1="0" x2="1" y2="1">
          <stop offset="0" stop-color="var(--card-light)"/>
          <stop offset="1" stop-color="var(--card-light-edge)"/>
        </linearGradient>
        <linearGradient id="stripe" x1="0" y1="0" x2="1" y2="0">
          <stop offset="0" stop-color="var(--teal-bright)"/>
          <stop offset="1" stop-color="var(--teal)"/>
        </linearGradient>
      </defs>
      <rect class="card-face" width="1080" height="590" fill="url(#frost)"/>
      <path class="accent-stripe" d="M86,240 Q560,424 1080,318" fill="none" stroke="url(#stripe)" stroke-width="9" stroke-linecap="round"/>
      <path class="dark-band" d="M0,209 Q560,440 1080,346 L1080,590 L0,590 Z" fill="var(--card-dark)"/>
    </svg>

    <div class="brand-name">Birchline Septic Solutions</div>

    <div class="owner">
      <div class="owner-name">Colin Vandro</div>
      <div class="owner-town">Maplecrest, OH</div>
    </div>
    <div class="divider"></div>
    <div class="phone">
      <svg class="phone-icon" viewBox="0 0 30 26" aria-hidden="true">
        <path d="M2,9 Q15,-1 28,9 L25,13 L20,11 L20,7 Q15,5 10,7 L10,11 L5,13 Z" fill="var(--teal)"/>
        <path d="M8,13 L22,13 L27,25 L3,25 Z" fill="var(--teal)"/>
        <circle cx="15" cy="19" r="3" fill="var(--card-dark)"/>
      </svg>
      <span>555-241-0387</span>
    </div>
  </div>
</div>
</body>
</html>
```